KBT Business Cards

We require business cards for our business. We would like a matte black back to the card, with our logo centred in the middle. The front side of the card is open to design.

Target Market(s)

Clients looking for legal services (professional)

Industry/Entity Type

Legal

Contact Information for Business Card

Doran Kelbrath
Partner
Mobile: 0461 738 524
Email: doran@kbtlaw.co
Website: www.kbtlaw.co
Level 3, 118 Wendmore Street
Sydney NSW 2000

Font styles to use
Other font styles liked:
• Avenir

Colors
f04a50
ffffff
1b1b1b

Requirements
Must have
• Black back with logo included in the centre of the card.
• Our font is Avenir.

```html
<!DOCTYPE html>
<html lang="en">
<head>
<meta charset="utf-8">
<title>KBT Business Cards</title>
<link rel="stylesheet" href="https://fonts.googleapis.com/css2?family=Arimo:wght@700&family=Lato:wght@400;700&display=swap">
<style>
  :root {
    --stage: #141414;
    --card: #1b1b1b;
    --card-edge: #242424;
    --ink: #ffffff;
    --ink-soft: #e6e6e6;
    --accent: #c8204a;
    --rule: #2c2c2c;
  }
  * { margin: 0; padding: 0; box-sizing: border-box; }
  html, body { width: 1200px; height: 900px; overflow: hidden; }
  body {
    background: var(--stage);
    font-family: "Lato", Arial, sans-serif;
    color: var(--ink);
    position: relative;
  }
  .card {
    position: absolute;
    left: 320px;
    width: 560px;
    height: 320px;
    background: var(--card);
    border: 1px solid var(--card-edge);
    border-radius: 22px;
    box-shadow: 0 18px 40px rgba(0,0,0,.55);
  }
  .card--back { top: 100px; }
  .card--front { top: 480px; }

  .wordmark {
    font-family: "Arimo", Arial, sans-serif;
    font-weight: 700;
    text-transform: uppercase;
    line-height: 0.98;
    color: var(--ink);
    letter-spacing: 0.01em;
  }
  .card--back .wordmark {
    position: absolute;
    left: 200px;
    top: 92px;
    font-size: 38px;
  }
  .card--back .site {
    position: absolute;
    left: 340px;
    top: 250px;
    font-size: 15px;
    color: var(--ink-soft);
    letter-spacing: 0.02em;
  }

  .brand {
    position: absolute;
    left: 290px;
    top: 46px;
    display: flex;
    align-items: center;
    gap: 18px;
  }
  .brand__square {
    width: 58px;
    height: 58px;
    background: var(--accent);
  }
  .card--front .wordmark { font-size: 25px; }

  .divider {
    position: absolute;
    left: 150px;
    right: 40px;
    top: 160px;
    height: 1px;
    background: var(--rule);
  }
  .address {
    position: absolute;
    right: 40px;
    top: 186px;
    text-align: right;
    font-size: 15px;
    line-height: 1.4;
    color: var(--ink-soft);
  }
  .person {
    position: absolute;
    left: 40px;
    top: 176px;
  }
  .person__name {
    font-size: 19px;
    font-weight: 700;
    text-transform: uppercase;
    color: var(--accent);
    letter-spacing: 0.02em;
  }
  .person__role {
    font-size: 15px;
    color: var(--ink-soft);
    margin: 2px 0 8px 8px;
  }
  .contacts { list-style: none; margin-left: 8px; }
  .contacts li {
    display: flex;
    align-items: center;
    gap: 10px;
    font-size: 15px;
    line-height: 1.45;
    color: var(--ink-soft);
  }
  .contacts svg { width: 12px; height: 12px; fill: var(--accent); flex: none; }
</style>
</head>
<body>
  <section class="card card--back" aria-label="Card back">
    <div class="wordmark">Kelbrath<br>Brandt Tate<br>Legal</div>
    <div class="site">www.kbtlaw.co</div>
  </section>

  <section class="card card--front" aria-label="Card front">
    <div class="brand">
      <span class="brand__square"></span>
      <div class="wordmark">Kelbrath<br>Brandt Tate<br>Legal</div>
    </div>
    <div class="divider"></div>
    <div class="address">Level 3, 118 Wendmore<br>Street, Sydney NSW 2000</div>
    <div class="person">
      <div class="person__name">Doran Kelbrath</div>
      <div class="person__role">Partner</div>
      <ul class="contacts">
        <li>
          <svg viewBox="0 0 12 12" aria-hidden="true"><path d="M1 4c0-2 2-3 3-3l1 2-1 1.2c.6 1.3 1.5 2.2 2.8 2.8L8 6l2 1c0 1-1 3-3 3C3.7 10 1 7.3 1 4z"/></svg>
          0461 738 524
        </li>
        <li>
          <svg viewBox="0 0 12 12" aria-hidden="true"><path d="M0 2h12v8H0z"/><path d="M0 2l6 4.5L12 2" fill="none" stroke="#1b1b1b" stroke-width="1.2"/></svg>
          doran@kbtlaw.co
        </li>
        <li>
          <svg viewBox="0 0 12 12" aria-hidden="true"><circle cx="6" cy="6" r="6"/><path d="M0 6h12M6 0c-3 3-3 9 0 12M6 0c3 3 3 9 0 12" fill="none" stroke="#1b1b1b" stroke-width=".9"/></svg>
          www.kbtlaw.co
        </li>
      </ul>
    </div>
  </section>
</body>
</html>
```